New Business Card Design Project

I need a design for business cards, i am an electrical business called "Corvane Electrical and Communications" i need the cards to be double sided with the company logo on the back (attached) the front needs to say my company name, web site, email address, telephone number, and ABN number and electrical license number. I am open to different arrangements of the information but would like the background to be incorporating something electrical or something that looks smart. open to all additional ideas also.

The company colours are orange and grey see logo attached.

Business Name: Corvane Electrical and Communications
Website: corvaneelectricalandcomms.example.com.au
Email: brent@corvaneelectricalandcomms.example.com.au
Telephone(mobile): 0481209736
ABN: 71208349162
Lic No: 418273D

Target Market(s)

Business entities, Project Managers, Accounts, Clients

Industry/Entity Type

Electrician

Contact Information for Business Card

I need a design for business cards, i am an electrical business called "Corvane Electrical and Communications" i need the cards to be double sided with the company logo on the back (attached) the front needs to say my company name

Font styles to use
Serif
Sans Serif

Colors
f37122
5c5c5c

Requirements
Must have
• Must have the Logo on the back open to different ways of it being on the back but had in mind to keep it central but again open to other options
Nice to have
• A real modern cool background that is eye catching yet contemporary
Should not have
• No backgrounds of a light bulb or plug or anything like that

```html
<!DOCTYPE html>
<html lang="en">
<head>
<meta charset="utf-8">
<title>Corvane Electrical and Communications – Business Card</title>
<link href="https://fonts.googleapis.com/css2?family=Source+Sans+3:wght@400;600;700&display=swap" rel="stylesheet">
<style>
  :root {
    --stage: #000000;
    --card: #333436;
    --card-edge: #3a3b3e;
    --orange: #f5b21f;
    --white: #ffffff;
    --soft: #e6e6e6;
  }
  * { box-sizing: border-box; margin: 0; padding: 0; }
  html, body {
    width: 1200px; height: 900px; overflow: hidden;
    background: var(--stage);
    font-family: "Source Sans 3", "Myriad Pro", sans-serif;
  }
  .stage { position: relative; width: 1200px; height: 900px; }
  .card {
    position: absolute; top: 270px;
    width: 457px; height: 282px;
    background: var(--card);
    border-radius: 14px;
    box-shadow: inset 0 0 0 1px var(--card-edge);
    overflow: hidden;
  }
  .card--front { left: 137px; }
  .card--back { left: 626px; }

  .wordmark { position: absolute; color: var(--white); font-weight: 600; line-height: 1; }
  .wordmark__dot { display: inline-block; border-radius: 50%; background: var(--orange); vertical-align: middle; }
  .wordmark__name { display: block; letter-spacing: 2px; text-transform: uppercase; }
  .wordmark__sub { display: block; text-transform: uppercase; letter-spacing: 0.6px; }

  .card--front .wordmark { left: 31px; top: 32px; }
  .card--front .wordmark__name { font-size: 38px; }
  .card--front .wordmark__sub { font-size: 9.5px; margin-top: 6px; }
  .card--front .wordmark__dot { width: 12px; height: 12px; margin-right: 8px; margin-top: -6px; }

  .card--back .wordmark { left: 0; right: 0; top: 112px; text-align: center; }
  .card--back .wordmark__name { font-size: 50px; }
  .card--back .wordmark__sub { font-size: 12.5px; margin-top: 8px; }
  .card--back .wordmark__dot { width: 15px; height: 15px; margin-right: 10px; margin-top: -8px; }

  .person { position: absolute; left: 196px; top: 126px; }
  .person__name { color: var(--orange); font-weight: 700; font-size: 17px; line-height: 20px; }
  .person__role { color: var(--white); font-size: 12px; line-height: 16px; }

  .contacts { position: absolute; left: 163px; top: 176px; list-style: none; }
  .contacts li { display: flex; align-items: center; height: 19px; color: var(--white); font-size: 12px; }
  .contacts svg { width: 10px; height: 10px; margin-right: 6px; fill: var(--orange); flex: none; }

  .registration { position: absolute; left: 198px; top: 242px; font-size: 13px; font-weight: 700; color: var(--white); }
  .registration b { color: var(--orange); }
  .registration .sep { margin: 0 5px; }

  .web-rule {
    position: absolute; left: 0; right: 0; top: 233px;
    display: flex; align-items: center; gap: 10px;
    color: var(--orange); font-weight: 700; font-size: 13.5px;
  }
  .web-rule::before, .web-rule::after { content: ""; flex: 1; height: 1px; background: var(--orange); }
</style>
</head>
<body>
<main class="stage">
  <section class="card card--front">
    <div class="wordmark">
      <span class="wordmark__name"><span class="wordmark__dot"></span>Corvane</span>
      <span class="wordmark__sub">Electrical &amp; Communications</span>
    </div>
    <div class="person">
      <p class="person__name">Brent Hollis</p>
      <p class="person__role">Director</p>
    </div>
    <ul class="contacts">
      <li><svg viewBox="0 0 10 10"><path d="M2 0.5 L3.6 2.6 L2.7 3.6 Q4 6 6.4 7.3 L7.4 6.4 L9.5 8 L8.4 9.5 Q4 9.3 0.5 1.6 Z"/></svg>0481209736</li>
      <li><svg viewBox="0 0 10 10"><path d="M0.5 2 H9.5 V8 H0.5 Z M0.9 2.4 L5 5.4 L9.1 2.4" stroke="#333436" stroke-width="0.8"/></svg>brent@corvaneelectricalandcomms.example.com.au</li>
      <li><svg viewBox="0 0 10 10"><circle cx="5" cy="5" r="4.5"/><path d="M3 3.5 Q4.5 2.5 5 4 Q6 5 5 6.5 M6.5 2 Q7.5 3.5 7 4.5" stroke="#333436" stroke-width="0.8" fill="none"/></svg>corvaneelectricalandcomms.example.com.au</li>
    </ul>
    <p class="registration"><b>ABN:</b> 71208349162<span class="sep">|</span><b>Lic No:</b> 418273D</p>
  </section>

  <section class="card card--back">
    <div class="wordmark">
      <span class="wordmark__name"><span class="wordmark__dot"></span>Corvane</span>
      <span class="wordmark__sub">Electrical &amp; Communications</span>
    </div>
    <p class="web-rule">corvaneelectricalandcomms.example.com.au</p>
  </section>
</main>
</body>
</html>
```